Chateau de Vermirelle multiple flyers

PRICE OFFERED IS PER FLYER IE: €139 PER FLYER OR €695 TOTAL WITH OTHERS TO FOLLOW

I want to creat a common design across a range of flyers that I will be handing out to visitors to our Christmas market, but will also be used throughout the year and years to come. The final design will need to be adapted so the copy can be translated into french as well as English. So I would need an ai or paint version as well as pdf's etc.

There are 5 flyers to be designed at this stage the PRICE OFFERED IS PER FLYER IE: €139 PER FLYER OR €695 TOTAL WITH OTHERS TO FOLLOW

1. Seminars at the chateau - 4 page 1/3 A4 double sided (No longer referring to full chateau rental)
2. Accomodation at the chateau 2 page 1/3 A4 double sided (Seasons simplified now: Peak = July & August and Christmas week; High, June and September. Low: Rest of year.)
3. QBVA 2 Award in Wine and Spirits 4 page 1/3 A4 double sided
See current offering at
http://www.valcharmille.example/experiences-and-tours/wine-tours/qbva-level-2-loire-valley-derek-pallister/#1467282665644-f1124b7e-5513

With photos here:
https://www.filecrate.example/sh/qpt482nzkdbvxar/AAAX3mRTyLpoW-Bnuk7hjdzke?dl=0

4. Valentine's/Romantic package 2 page 1/3 A4 double sided
5. Mothers Day package 2 page 1/3 A4 double sided.

The first two are very urgent as need to be available by Wednesday 7th December to go to print.

In the future we will be looking to add to the range with:

6. Wedding Brochure - 6 page 1/3 A4 double sided
7. Group celebrations - 6 page 1/3 A4 double sided
8. Pamper/Wellness package - 2 page 1/3 A4 double sided
9. Activity Break - 2 page 1/3 A4 double sided.

I have attached some examples of what we have to date, which are not consistent. As well as some excel spreadhseets which explain the packages. Along with an architects plan of the ground floor (may help with the seminar brochure.)

I have also provided a link to our gallery of photos that can be used and a couple of videos to give you a feel for the place.

https://www.filecrate.example/sh/k7vbnrzq2pwdoyt/AACJXNsPuelk8BHdrt2VhLmYe?dl=0

Target Market(s)

Adults aged 34 plus.
Seminars = Local businesses
Accommodation = 34 plus high income
Wedding = Females 28 plus high income

Requirements
Must have
• Demonstrates 5 star luxury and quality.

```html
<!DOCTYPE html>
<html lang="en">
<head>
<meta charset="utf-8">
<title>Chateau de Vermirelle – Seminar Price List Spread</title>
<link rel="stylesheet" href="https://fonts.googleapis.com/css2?family=Cormorant+Garamond:wght@400;600&family=Lato:wght@400;700&family=Great+Vibes&display=swap">
<style>
  :root{
    --backdrop:#d9e2b0;
    --paper:#f8f8f6;
    --paper-shade:#ecece8;
    --ink:#3a3a3a;
    --ink-soft:#6b6b6b;
    --gold:#c9a46a;
    --sand:#e2c794;
    --plum:#8a2a4f;
    --rule:#cfcfcf;
    --photo-green:#6f8a4e;
    --photo-stone:#b9c2cf;
    --photo-teal:#5f8f82;
    --photo-warm:#cdb8a0;
    --plan:#e3e3df;
  }
  *{margin:0;padding:0;box-sizing:border-box;}
  html,body{width:1200px;height:701px;overflow:hidden;background:var(--backdrop);}
  body{font-family:"Lato",Arial,sans-serif;color:var(--ink);}

  .spread{position:absolute;left:160px;top:40px;width:880px;height:622px;display:flex;
    box-shadow:0 10px 30px rgba(60,70,20,.18);}
  .page{position:relative;width:440px;height:622px;background:var(--paper);}
  .page--left{background:linear-gradient(to left,var(--paper-shade) 0,var(--paper) 30px);}
  .page--right{background:linear-gradient(to right,var(--paper-shade) 0,var(--paper) 30px);}

  /* Photo collage: flat placeholder blocks */
  .photo{position:absolute;}
  .photo--gardens{left:40px;top:80px;width:190px;height:170px;background:var(--photo-green);}
  .photo--chateau{left:232px;top:40px;width:178px;height:198px;background:var(--photo-stone);}
  .photo--pool{left:40px;top:252px;width:183px;height:122px;background:var(--photo-teal);}
  .photo--couple{left:225px;top:240px;width:185px;height:134px;background:var(--photo-warm);}

  .tagline{position:absolute;left:120px;top:212px;width:220px;font-family:"Great Vibes",cursive;
    font-size:30px;line-height:30px;color:var(--plum);}
  .tagline span{display:block;padding-left:44px;}

  .intro{position:absolute;left:40px;top:396px;width:370px;font-size:7.2px;line-height:11px;color:var(--ink-soft);}

  .folio{position:absolute;bottom:18px;font-size:6.5px;color:var(--ink-soft);letter-spacing:.5px;}
  .folio--left{left:40px;}
  .folio--right{right:40px;}
  .folio b{font-weight:700;margin-right:10px;}
  .folio--right b{margin:0 0 0 10px;}

  /* Right page */
  .brand{position:absolute;top:34px;left:0;width:100%;text-align:center;font-family:"Cormorant Garamond",Georgia,serif;
    font-size:11px;letter-spacing:3px;color:var(--ink-soft);text-transform:uppercase;}
  .title{position:absolute;top:54px;left:0;width:100%;text-align:center;font-family:"Cormorant Garamond",Georgia,serif;
    font-weight:600;font-size:28px;line-height:34px;color:var(--gold);}
  .title-rule{position:absolute;top:96px;left:170px;width:100px;height:1px;background:var(--gold);}

  .rates{position:absolute;top:114px;left:40px;width:370px;border-collapse:collapse;font-size:6.6px;color:var(--ink);}
  .rates th{font-weight:400;color:var(--ink-soft);padding:0 3px 5px;text-align:center;vertical-align:bottom;border-bottom:1px solid var(--rule);}
  .rates th.rates__label{text-align:left;font-weight:700;color:var(--ink);font-size:7.5px;}
  .rates th.rates__key{font-weight:700;color:var(--ink);}
  .rates td{padding:3.2px 3px;text-align:center;color:var(--ink-soft);}
  .rates td:first-child{text-align:left;color:var(--ink);border-right:1px solid var(--rule);}

  .includes{position:absolute;left:40px;top:378px;width:206px;height:88px;background:var(--sand);padding:12px 14px;
    font-size:7px;line-height:11px;color:#4a3a22;list-style:none;}
  .includes li{padding-left:9px;position:relative;margin-bottom:6px;}
  .includes li::before{content:"";position:absolute;left:0;top:4px;width:3px;height:3px;background:#4a3a22;}

  .floorplan{position:absolute;left:262px;top:374px;width:148px;height:72px;background:var(--plan);}
  .floorplan-caption{position:absolute;left:262px;top:454px;width:148px;font-size:6.5px;line-height:10px;color:var(--ink-soft);}
</style>
</head>
<body>
<div class="spread">
  <section class="page page--left">
    <div class="photo photo--gardens" role="img" aria-label="Photo: aerial view of the formal chateau gardens and parkland"></div>
    <div class="photo photo--chateau" role="img" aria-label="Photo: chateau facade with turrets"></div>
    <div class="photo photo--pool" role="img" aria-label="Photo: swimming pool by the lawn with champagne and glasses"></div>
    <div class="photo photo--couple" role="img" aria-label="Photo: wedding couple seated in an elegant salon"></div>
    <p class="tagline">share a<span>beautiful moment</span></p>
    <p class="intro">Step into a setting where history and comfort meet. Our rooms open onto quiet gardens, the pool glows in the late afternoon sun, and every detail is prepared so that you and your guests can simply enjoy the moment together, in the heart of the Loire Valley.</p>
    <p class="folio folio--left"><b>12</b>Brochure</p>
  </section>

  <section class="page page--right">
    <p class="brand">Chateau de Vermirelle</p>
    <h1 class="title">Price List</h1>
    <div class="title-rule"></div>

    <table class="rates">
      <thead>
        <tr>
          <th class="rates__label">Function Spaces</th>
          <th>Surface<br>(m²)</th>
          <th>Theatre</th>
          <th>U-shape</th>
          <th>Boardroom</th>
          <th>Half day<br>€</th>
          <th class="rates__key">Full day<br>€</th>
        </tr>
      </thead>
      <tbody>
        <tr><td>Grand Salon</td><td>120</td><td>90</td><td>40</td><td>36</td><td>650</td><td>1100</td></tr>
        <tr><td>Library</td><td>65</td><td>45</td><td>24</td><td>20</td><td>420</td><td>720</td></tr>
        <tr><td>Dining Room</td><td>90</td><td>60</td><td>30</td><td>28</td><td>520</td><td>880</td></tr>
        <tr><td>Orangery</td><td>110</td><td>80</td><td>36</td><td>32</td><td>600</td><td>1000</td></tr>
        <tr><td>Blue Salon</td><td>48</td><td>30</td><td>18</td><td>16</td><td>340</td><td>580</td></tr>
        <tr><td>Billiard Room</td><td>42</td><td>24</td><td>16</td><td>14</td><td>300</td><td>520</td></tr>
        <tr><td>Chapel</td><td>55</td><td>40</td><td>20</td><td>18</td><td>360</td><td>620</td></tr>
        <tr><td>Terrace</td><td>150</td><td>100</td><td>44</td><td>40</td><td>480</td><td>820</td></tr>
        <tr><td>Winter Garden</td><td>70</td><td>50</td><td>26</td><td>22</td><td>440</td><td>760</td></tr>
        <tr><td>Cellar</td><td>60</td><td>40</td><td>22</td><td>20</td><td>380</td><td>650</td></tr>
        <tr><td>Stables Hall</td><td>180</td><td>140</td><td>50</td><td>44</td><td>700</td><td>1200</td></tr>
        <tr><td>Music Room</td><td>52</td><td>36</td><td>18</td><td>16</td><td>350</td><td>600</td></tr>
      </tbody>
    </table>

    <ul class="includes">
      <li>Coffee breaks with pastries included in every day rate</li>
      <li>Projector, screen and high speed wifi in all rooms</li>
      <li>Lunch served in the dining room from €38 per guest</li>
    </ul>

    <div class="floorplan" role="img" aria-label="Architect's ground floor plan of the chateau"></div>
    <p class="floorplan-caption">Ground floor plan showing the function rooms, terrace access and the private dining area for seminar guests.</p>

    <p class="folio folio--right">Seminars<b>13</b></p>
  </section>
</div>
</body>
</html>
```